Rebrand stationary with recently completed logo design

Need new business cards, thank you cards, letterhead, envelopes and presentation folders. The designs will be sent to a separate production firm so I need the files to be print ready.

My contact info
Reko Haliburn

Office 604-318-5047
Fax 604-371-8054

Email reko@glazemark.ca
website www.glazemark.ca

315-14720 62nd Avenue,
Langley, BC, V2K 3R8

Target Market(s)

Homeowners, businesses and contractors

Industry/Entity Type

Business

Font styles to use
Sans Serif

Colors
34a7d7

Requirements
Must have
• Like to have one side of the business card a solid color with the logo in all white. The side with all the text to be a white background
• I find the current blue on the front of the card with the white logo too dark.
Should not have
• Gradient colors

```html
<!DOCTYPE html>
<html lang="en">
<head>
<meta charset="utf-8">
<title>Glazemark Presentation Folder – Print Layout</title>
<link rel="stylesheet" href="https://fonts.googleapis.com/css2?family=Arimo:ital,wght@0,400;0,700;1,400&display=swap">
<style>
  :root {
    --panel-blue: #0a8ad0;
    --guide-cyan: #5fd0e8;
    --die-red: #d9252a;
    --fold-green: #6cc38a;
    --glue-grey: #d4d4d6;
    --paper: #ffffff;
    --ink-white: #ffffff;
    --note-ink: #3a3a3c;
    --brand-grey: #58595b;
    --brand-cyan: #2aa3d6;
    --photo-tone: #9aa4ab;
  }
  * { box-sizing: border-box; margin: 0; padding: 0; }
  html, body { width: 1200px; height: 959px; overflow: hidden; background: var(--paper); }
  body { font-family: "Arimo", Arial, sans-serif; }
  .folder { position: relative; width: 1200px; height: 959px; }
  .dieline { position: absolute; left: 0; top: 0; }

  .copy-block { position: absolute; color: var(--ink-white); font-size: 7px; line-height: 8.7px; text-align: justify; }
  .copy-block h2 { font-size: 7px; font-weight: 700; text-transform: uppercase; margin-bottom: 9px; line-height: 8px; }
  .copy-block p + p { margin-top: 5px; }
  .col-left { left: 101px; width: 198px; }
  .col-right { left: 344px; width: 198px; }

  .photo { position: absolute; width: 94px; height: 70px; background: linear-gradient(160deg, #c9d0d4, var(--photo-tone)); }

  .pocket-note { position: absolute; left: 146px; top: 553px; color: var(--note-ink); font-size: 19.5px; line-height: 22px; }

  .brand-lockup { position: absolute; left: 770px; top: 748px; width: 190px; height: 152px; transform: rotate(180deg); }
  .brand-square { position: absolute; left: 80px; top: 8px; width: 32px; height: 56px; background: var(--brand-grey); }
  .brand-name { position: absolute; left: 8px; top: 73px; width: 174px; text-align: center; font-size: 29px; font-weight: 400; color: var(--brand-grey); letter-spacing: 0.5px; line-height: 30px; }
  .brand-tagline { position: absolute; left: 8px; top: 105px; width: 174px; text-align: center; font-size: 11px; color: var(--brand-grey); letter-spacing: 0.6px; }
  .brand-web { position: absolute; left: 20px; top: 125px; width: 170px; font-size: 14px; font-style: italic; color: var(--brand-cyan); letter-spacing: 0.6px; display: flex; align-items: center; gap: 6px; }
</style>
</head>
<body>
<div class="folder">
  <svg class="dieline" width="1200" height="959" viewBox="0 0 1200 959">
    <rect x="45" y="0" width="555" height="697" fill="var(--panel-blue)"/>
    <rect x="47" y="697" width="38" height="261" fill="var(--glue-grey)"/>
    <rect x="1115" y="697" width="38" height="261" fill="var(--glue-grey)"/>
    <rect x="63" y="18" width="519" height="662" fill="none" stroke="var(--guide-cyan)" stroke-width="1"/>
    <rect x="618" y="18" width="518" height="660" fill="none" stroke="var(--guide-cyan)" stroke-width="1"/>
    <path d="M78,697 L108,500 Q116,477 148,477 L551,477 L551,697" fill="rgba(255,255,255,0.04)" stroke="var(--guide-cyan)" stroke-width="0.8"/>
    <line x1="329" y1="477" x2="329" y2="678" stroke="#2b4a66" stroke-width="1"/>
    <path d="M630,715 L1103,716 L1103,938 L712,938 Q662,936 650,880 Z" fill="none" stroke="var(--guide-cyan)" stroke-width="0.8"/>
    <g fill="none" stroke="var(--die-red)" stroke-width="1">
      <path d="M45,0 L1155,0"/>
      <path d="M45,0 L0,6 L0,418 A21,21 0 0 1 0,460 L0,688 L45,697"/>
      <path d="M1155,0 L1200,8 L1200,418 A21,21 0 0 0 1200,460 L1200,690 L1155,697"/>
      <path d="M45,697 L47,958 L528,958 Q555,957 558,930 L600,697"/>
      <path d="M600,697 L640,930 Q645,957 672,958 L1153,958 L1155,697"/>
      <path d="M215,805 L251,768 M389,768 L425,805 M215,853 L251,890 M389,890 L425,853"/>
    </g>
    <g fill="none" stroke="var(--fold-green)" stroke-width="1" stroke-dasharray="3 3">
      <path d="M600,0 L600,697 L1155,697 M1155,0 L1155,697"/>
    </g>
    <g fill="none" stroke="var(--ink-white)" stroke-width="1">
      <path d="M315,52 Q320,52 320,57 L320,74 Q320,79 324,79 Q320,79 320,84 L320,101 Q320,106 315,106"/>
      <path d="M315,144 Q320,144 320,149 L320,166 Q320,171 324,171 Q320,171 320,176 L320,193 Q320,198 315,198"/>
      <path d="M315,259 Q320,259 320,264 L320,281 Q320,286 324,286 Q320,286 320,291 L320,308 Q320,313 315,313"/>
    </g>
  </svg>

  <section class="copy-block col-left" style="top:52px">
    <h2>Solar Film</h2>
    <p>There are many benefits with our solar film products, they can help reduce the heat passing through your windows, reduce the glare often present on bright days, as well as reduce over 99% of the harmful ultraviolet rays that damage furnishings and cause skin damage.</p>
  </section>
  <section class="copy-block col-right" style="top:52px">
    <h2>Protection from the Sun</h2>
    <p>Our solar film can remove as much as 79% of the sun's total energy. Utilizing advanced metals and ceramic technology, we can offer products with very low reflectivity and high light transmission levels as well reflective film for maximum heat rejection and privacy.</p>
  </section>

  <section class="copy-block col-left" style="top:144px">
    <h2>Frosted Film</h2>
    <p>Once installed, frosted window film can increase your privacy, reduce the glare, or change a dated office environment to a more functional and appealing workplace.</p>
  </section>
  <section class="copy-block col-right" style="top:144px">
    <h2>Increased Privacy</h2>
    <p>Whether you are an architect, interior designer or homeowner, we have the products for your creative side.</p>
    <p>Bring out your creative side with custom frosted graphics. With different shades of frost you can control the amount of light and privacy required, use patterns and textured frosted film to customize your graphics even more. By mixing the various products, your glass becomes a blank canvas with endless possibilities.</p>
  </section>

  <section class="copy-block col-left" style="top:259px">
    <h2>Safety and Security Film</h2>
    <p>Ideal for glass where safety from potential injury is required or to delay the entry by an intruder.</p>
  </section>
  <section class="copy-block col-right" style="top:259px">
    <h2>Peace of Mind</h2>
    <p>Optically Clear and Long Lasting</p>
    <p>The abundance of glass in homes and businesses offer a great deal of light and openness, with that comes a higher degree of risk for injury. Crime, vandalism, natural disasters and everyday accidents exist but with security film from Glazemark those dangers can be greatly reduced.</p>
    <p>Clarivex security film is available in a variety of thicknesses as well as varying tint levels, the different products are available as an optically clear film to a highly reflective solar film to help reduce the heat gain in the summer months as well increasing the privacy through those windows.</p>
  </section>

  <div class="photo" style="left:103px;top:309px" role="img" aria-label="Storefront windows fitted with window film"></div>
  <div class="photo" style="left:203px;top:309px" role="img" aria-label="Bright office interior with filmed glass walls"></div>
  <div class="photo" style="left:103px;top:386px" role="img" aria-label="Frosted glass office partition"></div>
  <div class="photo" style="left:203px;top:386px" role="img" aria-label="Building entrance with tinted glass doors"></div>

  <p class="pocket-note">Here we can’t put the text<br>this area will be covered the pouch/pocket</p>

  <div class="brand-lockup">
    <div class="brand-square"></div>
    <div class="brand-name">GLAZEMARK</div>
    <div class="brand-tagline">GLASS CARE SPECIALISTS</div>
    <div class="brand-web">
      <svg width="11" height="11" viewBox="0 0 12 12" fill="none" stroke="var(--brand-cyan)" stroke-width="1">
        <circle cx="6" cy="6" r="5"/><ellipse cx="6" cy="6" rx="2.2" ry="5"/><path d="M1,6 H11 M2,3.3 H10 M2,8.7 H10"/>
      </svg>
      <span>www.glazemark.ca</span>
    </div>
  </div>
</div>
</body>
</html>
```